VORLE Diagnostics Pooling One Sheet

The process and concept for pooling is to target large populations of people; i.e. a school, prison, employer (where people are isolated by pods), then to test them all in one controllable group. By breaking down the pool size (ideally is 12 or 16 max) then when a positive pool pops up, the entity has the lab automatically reflex to test the whole pool to determine who is positive. During that exchange, several workflows could take place from the population that was being tested. This type of pooled testing is called Surveillance testing ,when it reflects, then it goes to Screening or Diagnostic testing.

The workflow is:
School/employer collects all patient information captured on a requisition form or electronically (w signature) and DOES NOT send to VORLE
School/employer collects individual specimens and labels them with a unique bar code (non-repeating and can include the DOB)
School/employer is responsible for housing and managing all the unique patient information for each individual specimen
School/employer delivers specimens to VORLE and School/employer directs VORLE what specimens are in what designated pool (one pool size for entire project)
When a pool is positive, VORLE notifies School/employer
When reflex testing in indicated for client, School/employer submits to VORLE on demand all patient information needed to process the reflexed option
VORLE reports back to School/employer in 12 hours the results of the retest
https://www.healthregistry-example.org/medical-devices/coronavirus-covid-19-and-medical-devices/pooled-sample-testing-and-screening-testing-covid-19
https://www.testmere.com/coronavirus-disease-covid-19/news/testmere-receives-authorization-covid-19-sample-pooling

Target Market(s)

Schools, Universities, Employers

Font styles to use
Sans Serif

Colors
85acd3
85cae6
34a6d7

Requirements
Must have
• VORLE branded along with an elegant yet clinical feel. have all contact information for VORLE Diagnostics. Go to www.vorledx.com for all info

```html
<!DOCTYPE html>
<html lang="en">
<head>
<meta charset="utf-8">
<title>VORLE Diagnostics – Pooling One Sheet</title>
<link href="https://fonts.googleapis.com/css2?family=Lato:wght@400;700;900&display=swap" rel="stylesheet">
<style>
  :root {
    --backdrop: #85cae6;
    --paper: #ffffff;
    --brand-blue: #1a8ed5;
    --brand-blue-deep: #0f7bcc;
    --navy: #2a3d4b;
    --footer-top: #1d4d93;
    --footer-bottom: #1a2f6b;
    --tick: #34a6d7;
    --ink: #1f2a33;
    --photo-light: #dbe9f2;
    --photo-mid: #a9cbe6;
  }
  * { box-sizing: border-box; margin: 0; padding: 0; }
  html, body { width: 1200px; height: 1200px; overflow: hidden; }
  body { background: var(--backdrop); font-family: "Lato", sans-serif; position: relative; }

  .sheet {
    position: absolute; left: 200px; top: 39px;
    width: 800px; height: 1122px;
    background: var(--paper); overflow: hidden;
  }

  .brand {
    position: absolute; left: 62px; top: 60px; height: 44px;
    display: flex; align-items: center; gap: 14px;
  }
  .brand-square { width: 38px; height: 38px; background: var(--navy); }
  .brand-name { font-weight: 900; font-size: 36px; color: var(--navy); letter-spacing: 0.5px; }

  .intro-band {
    position: absolute; left: 0; top: 150px; width: 800px; height: 320px;
    background: linear-gradient(180deg, var(--brand-blue) 0%, var(--brand-blue-deep) 100%);
  }
  .intro-text {
    position: absolute; left: 59px; top: 174px; width: 308px;
    color: #fff; font-size: 15.8px; line-height: 18.8px;
  }

  .hero-hex { position: absolute; left: 0; top: 0; width: 800px; height: 560px; }

  .workflow-title {
    position: absolute; left: 59px; top: 505px; width: 251px; height: 44px;
    background: var(--navy); color: #fff; border-radius: 0 22px 22px 0;
    font-weight: 900; font-size: 22px; line-height: 44px; padding-left: 18px;
  }

  .workflow-list {
    position: absolute; left: 59px; top: 569px; width: 662px; list-style: none;
  }
  .workflow-list li {
    position: relative; padding-left: 31px; margin-bottom: 8.6px;
    font-size: 15.6px; line-height: 18.8px; color: var(--ink);
  }
  .workflow-list .tick { position: absolute; left: 0; top: 1px; width: 18px; height: 18px; }

  .reference-band {
    position: absolute; left: 0; top: 882px; width: 800px; height: 151px;
    background: linear-gradient(100deg, var(--brand-blue) 0%, #2a9ae0 60%, var(--brand-blue) 100%);
  }
  .reference-rule { position: absolute; left: 64px; top: 910px; width: 2px; height: 95px; background: #9fd3f3; }
  .reference-links {
    position: absolute; left: 90px; top: 910px; width: 690px;
    color: #fff; font-weight: 700; font-size: 15.5px; line-height: 20.5px; white-space: nowrap;
  }
  .reference-links p + p { margin-top: 10px; }

  .contact-bar {
    position: absolute; left: 0; top: 1032px; width: 800px; height: 90px;
    background: linear-gradient(180deg, var(--footer-top), var(--footer-bottom));
    color: #fff; font-size: 13px; line-height: 16px;
  }
  .contact-item {
    position: absolute; top: 0; height: 90px;
    display: flex; align-items: center; gap: 8px;
  }
  .contact-item svg { width: 15px; height: 15px; flex: none; }
  .contact-phone { left: 62px; }
  .contact-address { left: 248px; }
  .contact-email { left: 474px; }
  .contact-web { left: 632px; }
</style>
</head>
<body>
<main class="sheet">
  <header class="brand">
    <span class="brand-square"></span>
    <span class="brand-name">VORLE Diagnostics</span>
  </header>

  <section class="intro-band"></section>

  <svg class="hero-hex" viewBox="0 0 800 560" role="img" aria-label="Photo of a clinician in protective suit and face shield taking a swab sample from a patient">
    <defs>
      <linearGradient id="heroFill" x1="0" y1="0" x2="1" y2="1">
        <stop offset="0" stop-color="var(--photo-light)"/>
        <stop offset="0.6" stop-color="#eaf2f7"/>
        <stop offset="1" stop-color="var(--photo-mid)"/>
      </linearGradient>
    </defs>
    <polygon points="620,31 837,156 837,406 620,531 403,406 403,156" fill="#fff"/>
    <polygon points="620,46 824,164 824,399 620,516 416,399 416,164" fill="url(#heroFill)"/>
  </svg>

  <p class="intro-text">The process and concept for pooling is to target large populations of people; i.e. a school, prison, employer (where people are isolated by pods), then to test them all in one controllable group. By breaking down the pool size (ideally is 12 or 16 max) then when a positive pool pops up, the entity has the lab automatically reflex to test the whole pool to determine who is positive. During that exchange, several workflows could take place from the population that was being tested. This type of pooled testing is called Surveillance testing, when it reflects, then it goes to Screening or Diagnostic testing.</p>

  <h2 class="workflow-title">THE WORKFLOW IS</h2>

  <ul class="workflow-list">
    <li><svg class="tick" viewBox="0 0 18 18"><circle cx="9" cy="9" r="7.8" fill="none" stroke="var(--tick)" stroke-width="1.6"/><path d="M5.5 9.2l2.4 2.3 4.4-4.6" fill="none" stroke="var(--tick)" stroke-width="1.6"/></svg>School/employer collects all patient information captured on a requisition form or electronically (w signature) and DOES NOT send to VORLE</li>
    <li><svg class="tick" viewBox="0 0 18 18"><circle cx="9" cy="9" r="7.8" fill="none" stroke="var(--tick)" stroke-width="1.6"/><path d="M5.5 9.2l2.4 2.3 4.4-4.6" fill="none" stroke="var(--tick)" stroke-width="1.6"/></svg>School/employer collects individual specimens and labels them with a unique bar code (non&#8209;repeating and can include the DOB)</li>
    <li><svg class="tick" viewBox="0 0 18 18"><circle cx="9" cy="9" r="7.8" fill="none" stroke="var(--tick)" stroke-width="1.6"/><path d="M5.5 9.2l2.4 2.3 4.4-4.6" fill="none" stroke="var(--tick)" stroke-width="1.6"/></svg>School/employer is responsible for housing and managing all the unique patient information for each individual specimen</li>
    <li><svg class="tick" viewBox="0 0 18 18"><circle cx="9" cy="9" r="7.8" fill="none" stroke="var(--tick)" stroke-width="1.6"/><path d="M5.5 9.2l2.4 2.3 4.4-4.6" fill="none" stroke="var(--tick)" stroke-width="1.6"/></svg>School/employer delivers specimens to VORLE and School/employer directs VORLE what specimens are in what designated pool (one pool size for entire project)</li>
    <li><svg class="tick" viewBox="0 0 18 18"><circle cx="9" cy="9" r="7.8" fill="none" stroke="var(--tick)" stroke-width="1.6"/><path d="M5.5 9.2l2.4 2.3 4.4-4.6" fill="none" stroke="var(--tick)" stroke-width="1.6"/></svg>When a pool is positive, VORLE notifies School/employer</li>
    <li><svg class="tick" viewBox="0 0 18 18"><circle cx="9" cy="9" r="7.8" fill="none" stroke="var(--tick)" stroke-width="1.6"/><path d="M5.5 9.2l2.4 2.3 4.4-4.6" fill="none" stroke="var(--tick)" stroke-width="1.6"/></svg>When reflex testing in indicated for client, School/employer submits to VORLE on demand all patient information needed to process the reflexed option</li>
    <li><svg class="tick" viewBox="0 0 18 18"><circle cx="9" cy="9" r="7.8" fill="none" stroke="var(--tick)" stroke-width="1.6"/><path d="M5.5 9.2l2.4 2.3 4.4-4.6" fill="none" stroke="var(--tick)" stroke-width="1.6"/></svg>VORLE reports back to School/employer in 12 hours the results of the retest</li>
  </ul>

  <section class="reference-band"></section>
  <span class="reference-rule"></span>
  <div class="reference-links">
    <p>https://www.healthregistry-example.org/medical-devices/coronavirus-<br>covid-19-and-medical-devices/pooled-sample-testing-and-screening-testing-covid-19</p>
    <p>https://www.testmere.com/coronavirus-disease-covid-19/news/<br>testmere-receives-authorization-covid-19-sample-pooling</p>
  </div>

  <footer class="contact-bar">
    <div class="contact-item contact-phone">
      <svg viewBox="0 0 16 16"><path d="M3.2 1.5l2.6 2.6-1.4 1.9c.9 2 2.6 3.7 4.6 4.6l1.9-1.4 2.6 2.6-1.7 2.2C6.6 13.8 2.2 9.4 1 3.2z" fill="none" stroke="#fff" stroke-width="1.4" stroke-linejoin="round"/></svg>
      <span>800-555-VORL (8675)</span>
    </div>
    <div class="contact-item contact-address">
      <svg viewBox="0 0 16 16"><path d="M8 1a5 5 0 0 0-5 5c0 3.6 5 9 5 9s5-5.4 5-9a5 5 0 0 0-5-5z" fill="#fff"/><circle cx="8" cy="6" r="1.8" fill="var(--footer-bottom)"/></svg>
      <span>1420 Meridian Way Suite B<br>Fairhaven, MD 21000</span>
    </div>
    <div class="contact-item contact-email">
      <svg viewBox="0 0 16 16"><rect x="1" y="3.5" width="14" height="9.5" fill="none" stroke="#fff" stroke-width="1.4"/><path d="M1 3.5l7 5.5 7-5.5" fill="none" stroke="#fff" stroke-width="1.4"/></svg>
      <span>info@vorledx.com</span>
    </div>
    <div class="contact-item contact-web">
      <svg viewBox="0 0 16 16"><circle cx="8" cy="8" r="6.5" fill="none" stroke="#fff" stroke-width="1.3"/><ellipse cx="8" cy="8" rx="2.8" ry="6.5" fill="none" stroke="#fff" stroke-width="1.1"/><path d="M1.5 8h13" stroke="#fff" stroke-width="1.1"/></svg>
      <span>www.vorledx.com</span>
    </div>
  </footer>
</main>
</body>
</html>
```